RESIDENTIAL CONSTRUCTION

We are a company that specializes in building custom residential homes, the design should also emphasize that quality and service is our priority.

Industry/Entity Type

Construction Company

Contact Information for Business Card

Contact Person: Marcus Lindqvist
Company Address: 273 West Alder Ave San Jose , Ca 95380
Phone Number : 408-731-2946
Email Address: Stoneridgehomes517@mailvista.net

Font styles to use
Sans Serif

Colors
ec1f27

Requirements
Must have
• CSLB # 7362015
Nice to have
• needs to have same color as logo i uploaded, we will be printing these on a clear plastic card.

```html
<!DOCTYPE html>
<html lang="en">
<head>
<meta charset="utf-8">
<title>Stoneridge Homes — Business Card</title>
<link href="https://fonts.googleapis.com/css2?family=Roboto+Condensed:wght@700&family=Roboto:wght@400&display=swap" rel="stylesheet">
<style>
  :root {
    --brand-red: #ec1f27;
    --ink-black: #141414;
    --text-grey: #4a4a4a;
    --card-white: #f4f4f4;
    --backdrop: #d9d9d9;
    --band-dark: #2a2a2a;
  }
  html, body {
    margin: 0;
    padding: 0;
    width: 1200px;
    height: 826px;
    overflow: hidden;
    background: var(--backdrop);
  }
  .canvas {
    position: relative;
    width: 1200px;
    height: 826px;
  }
  .business-card {
    position: absolute;
    left: 380px;
    top: 28px;
    width: 440px;
    height: 770px;
    background: var(--card-white);
    box-shadow: 0 2px 10px rgba(0,0,0,0.18);
    overflow: hidden;
  }
  .brand-lockup {
    position: absolute;
    left: 62px;
    top: 92px;
    display: flex;
    align-items: center;
    gap: 12px;
    white-space: nowrap;
  }
  .brand-square {
    flex: none;
    width: 34px;
    height: 34px;
    background: var(--ink-black);
  }
  .brand-name {
    font-family: "Roboto Condensed", sans-serif;
    font-weight: 700;
    font-size: 38px;
    line-height: 1;
    color: var(--brand-red);
    white-space: nowrap;
  }
  .contact-name {
    position: absolute;
    left: 70px;
    top: 438px;
    margin: 0;
    font-family: "Roboto Condensed", sans-serif;
    font-weight: 700;
    font-size: 27px;
    color: var(--brand-red);
    letter-spacing: 0.3px;
    white-space: nowrap;
  }
  .contact-details {
    position: absolute;
    left: 74px;
    top: 512px;
    font-family: "Roboto", sans-serif;
    font-weight: 400;
    font-size: 18px;
    line-height: 24px;
    color: var(--text-grey);
    white-space: nowrap;
  }
  .contact-details p { margin: 0; }
  .contact-details .licence { margin-top: 6px; }
  .contact-details .phone { margin-top: 10px; }
  .contact-details .website { margin-top: 24px; }
  .ruler-band {
    position: absolute;
    left: 0;
    bottom: 0;
    width: 440px;
    height: 52px;
    background: linear-gradient(to bottom, rgba(42,42,42,0) 0%, rgba(42,42,42,0.35) 55%, var(--band-dark) 100%);
  }
</style>
</head>
<body>
<div class="canvas">
  <div class="business-card">
    <div class="brand-lockup">
      <span class="brand-square"></span>
      <span class="brand-name">STONERIDGE HOMES</span>
    </div>

    <h1 class="contact-name">MARCUS LINDQVIST</h1>

    <div class="contact-details">
      <p class="address">273 West Alder Ave San Jose</p>
      <p class="address">Ca 95380</p>
      <p class="licence">CSLB # 7362015</p>
      <p class="phone">P. 408-731-2946</p>
      <p class="email">Stoneridgehomes517@mailvista.net</p>
      <p class="website">www.stoneridgehomes.net</p>
    </div>

    <div class="ruler-band" role="img" aria-label="Decorative measuring-ruler edge along the bottom of the card"></div>
  </div>
</div>
</body>
</html>
```